Consulting Company PowerPoint Template Design

We are looking for an updated PowerPoint template design or our 55 person energy consulting firm (K7) based in San Francisco (www.kseven-example.com). We would like two versions of the same PowerPoint template in a 16:9 and 4:3 format with our existing logo.

We have an existing color scheme and template and are seeking your help to polish/update the template design for wide format and create a flexible template that is easy to use with content from Excel and Word. Our current template, and a couple of examples that we like are attached.

Specific requests include:

• Dark background for slide title
• A narrow section header
• Maximizing white space for content
• A limited number of well designed Master template layouts to choose from
• A selection of title and section header slides that are not San Francisco specific with some variety to chose from ideally with a focus on energy or nature, graphics/visuals.

For examples of energy specific templates see:
https://www.brightslidehub.example/energy/powerpoint-templates/0.html

Requirements
Must have
• Must use our logo but open to other designs, fonts, and styles for the PowerPoint template.
• Please use our existing color scheme found in the attached Excel file.
• Also we would like the ability to easily copy and paste from our existing/original template to the new template. In other words we would like backward compatibility to apply the new template format to our old PowerPoints that use our existing template.

```html
<!DOCTYPE html>
<html lang="en">
<head>
<meta charset="utf-8">
<title>K7 Slide – Options Path</title>
<link href="https://fonts.googleapis.com/css2?family=Raleway:wght@500;700&family=Titillium+Web:wght@600;700&display=swap" rel="stylesheet">
<style>
  :root {
    --navy: #064a6b;
    --gold: #d2a960;
    --gold-soft: #c9a463;
    --sky: #a9d0f0;
    --slate-1: #2e4a68;
    --slate-2: #3a5f85;
    --slate-3: #1f3d5c;
    --slate-4: #2a4767;
    --ink: #1e3652;
    --white: #ffffff;
  }
  * { margin: 0; padding: 0; box-sizing: border-box; }
  html, body { width: 1200px; height: 900px; overflow: hidden; background: var(--white); }
  .slide { position: relative; width: 1200px; height: 900px; background: var(--white); overflow: hidden; }

  .slide-header {
    position: absolute; left: 0; top: 0; width: 1200px; height: 66px;
    background: var(--navy);
  }
  .slide-title {
    position: absolute; left: 16px; top: 10px;
    font-family: "Titillium Web", sans-serif; font-weight: 600;
    font-size: 31px; letter-spacing: 0.5px; color: var(--white); line-height: 44px;
  }
  .slide-title .accent { color: var(--gold); }
  .header-rule { position: absolute; left: 0; top: 66px; }

  .brand-badge {
    position: absolute; left: 1112px; top: 3px; width: 80px; height: 80px;
    border-radius: 50%; background: var(--white); border: 4px solid var(--navy);
    display: flex; align-items: center; justify-content: center;
    font-family: "Titillium Web", sans-serif; font-weight: 700; font-size: 30px; color: var(--navy);
  }

  .options-path { position: absolute; left: 0; top: 0; }
  .option-label { font-family: "Raleway", sans-serif; font-weight: 700; font-size: 21px; }
  .option-note { font-family: "Raleway", sans-serif; font-weight: 500; font-size: 13.5px; }

  .slide-footer {
    position: absolute; left: 0; top: 855px; width: 1200px; height: 45px;
    background: var(--navy);
  }
  .footer-name {
    position: absolute; left: 9px; top: 6px;
    font-family: "Titillium Web", sans-serif; font-weight: 700; font-size: 24px; color: var(--white);
    line-height: 32px;
  }
  .page-tab { position: absolute; left: 1090px; top: 855px; }
  .page-number {
    position: absolute; left: 1136px; top: 862px;
    font-family: "Titillium Web", sans-serif; font-weight: 600; font-size: 21px; color: var(--white);
  }
</style>
</head>
<body>
<div class="slide">
  <header class="slide-header">
    <h1 class="slide-title"><span class="accent">PROJECT</span> TITLE HERE</h1>
  </header>
  <svg class="header-rule" width="1200" height="10" viewBox="0 0 1200 10">
    <polygon points="0,0 1200,0 1200,2 1110,8 0,8" fill="var(--gold)"/>
  </svg>
  <div class="brand-badge">K7</div>

  <svg class="options-path" width="1200" height="900" viewBox="0 0 1200 900">
    <!-- path line -->
    <path d="M0,578 L175,415 Q232,358 290,415 L335,452 Q362,474 389,452 L432,415 Q490,358 548,415 L592,452 Q619,474 646,452 L690,415 Q747,358 805,415 L850,452 Q877,474 904,452 L945,415 Q1002,360 1060,410 L1082,412 L1165,351"
          fill="none" stroke="var(--sky)" stroke-width="6" stroke-linejoin="round" stroke-linecap="round"/>
    <polygon points="1192,331 1176,380 1139,333" fill="var(--sky)"/>

    <!-- top row -->
    <g transform="translate(237,495)">
      <rect x="-80" y="-80" width="160" height="160" rx="30" transform="rotate(45)" fill="var(--slate-1)"/>
      <g class="icon-bulb" fill="var(--sky)" stroke="var(--sky)" stroke-width="2.5" stroke-linecap="round">
        <circle cx="0" cy="-50" r="13" stroke="none"/>
        <rect x="-6" y="-38" width="12" height="10" rx="2" stroke="none"/>
        <line x1="-22" y1="-50" x2="-27" y2="-50"/><line x1="22" y1="-50" x2="27" y2="-50"/>
        <line x1="-16" y1="-66" x2="-20" y2="-70"/><line x1="16" y1="-66" x2="20" y2="-70"/>
        <line x1="0" y1="-70" x2="0" y2="-75"/>
      </g>
      <text class="option-label" x="0" y="23" text-anchor="middle" fill="var(--sky)">Option 01</text>
    </g>
    <g transform="translate(490,495)">
      <rect x="-80" y="-80" width="160" height="160" rx="30" transform="rotate(45)" fill="var(--gold-soft)"/>
      <g class="icon-moneybag" fill="var(--ink)">
        <path d="M-8,-75 L8,-75 L4,-66 L-4,-66 Z"/>
        <path d="M-5,-64 C-22,-56 -22,-30 -14,-28 L14,-28 C22,-30 22,-56 5,-64 Z"/>
        <text x="0" y="-38" text-anchor="middle" font-family="Raleway, sans-serif" font-weight="700" font-size="16" fill="var(--gold-soft)">$</text>
      </g>
      <text class="option-label" x="0" y="23" text-anchor="middle" fill="var(--ink)">Option 02</text>
    </g>
    <g transform="translate(747,495)">
      <rect x="-80" y="-80" width="160" height="160" rx="30" transform="rotate(45)" fill="var(--slate-2)"/>
      <text class="option-note" text-anchor="middle" fill="var(--white)">
        <tspan x="0" y="-28">Duis tortor,</tspan>
        <tspan x="0" y="-11">suscipit eget,</tspan>
        <tspan x="0" y="6">imperdiet nec,</tspan>
        <tspan x="0" y="23">imperdiet</tspan>
      </text>
    </g>
    <g transform="translate(1000,495)">
      <rect x="-80" y="-80" width="160" height="160" rx="30" transform="rotate(45)" fill="var(--slate-3)"/>
      <text class="option-note" text-anchor="middle" fill="var(--white)">
        <tspan x="0" y="-28">Duis tortor,</tspan>
        <tspan x="0" y="-11">suscipit eget,</tspan>
        <tspan x="0" y="6">imperdiet nec,</tspan>
        <tspan x="0" y="23">imperdiet</tspan>
      </text>
    </g>

    <!-- bottom row -->
    <g transform="translate(120,607)">
      <rect x="-80" y="-80" width="160" height="160" rx="30" transform="rotate(45)" fill="var(--slate-4)"/>
      <text class="option-note" text-anchor="middle" fill="var(--white)">
        <tspan x="0" y="-19">Duis tortor,</tspan>
        <tspan x="0" y="-2">suscipit eget,</tspan>
        <tspan x="0" y="15">imperdiet nec,</tspan>
        <tspan x="0" y="32">imperdiet</tspan>
      </text>
    </g>
    <g transform="translate(363,607)">
      <rect x="-80" y="-80" width="160" height="160" rx="30" transform="rotate(45)" fill="var(--gold-soft)"/>
      <text class="option-note" text-anchor="middle" fill="var(--ink)">
        <tspan x="0" y="-19">Duis tortor,</tspan>
        <tspan x="0" y="-2">suscipit eget,</tspan>
        <tspan x="0" y="15">imperdiet nec,</tspan>
        <tspan x="0" y="32">imperdiet</tspan>
      </text>
    </g>
    <g transform="translate(620,600)">
      <rect x="-80" y="-80" width="160" height="160" rx="30" transform="rotate(45)" fill="var(--slate-2)"/>
      <text class="option-label" x="0" y="-3" text-anchor="middle" fill="var(--sky)">Option 03</text>
      <g class="icon-search" fill="none" stroke="var(--sky)" stroke-width="5" stroke-linecap="round">
        <circle cx="4" cy="40" r="12"/>
        <line x1="-4" y1="49" x2="-16" y2="61"/>
      </g>
    </g>
    <g transform="translate(875,600)">
      <rect x="-80" y="-80" width="160" height="160" rx="30" transform="rotate(45)" fill="var(--slate-3)"/>
      <text class="option-label" x="0" y="-3" text-anchor="middle" fill="var(--sky)">Option 04</text>
      <g class="icon-coins" fill="var(--sky)">
        <ellipse cx="0" cy="32" rx="20" ry="5"/>
        <rect x="-20" y="36" width="40" height="5" rx="2.5"/>
        <rect x="-20" y="43" width="40" height="5" rx="2.5"/>
        <rect x="-20" y="50" width="40" height="5" rx="2.5"/>
        <rect x="-20" y="57" width="40" height="5" rx="2.5"/>
      </g>
    </g>
  </svg>

  <footer class="slide-footer">
    <p class="footer-name">Kinetic+Resource Economics</p>
  </footer>
  <svg class="page-tab" width="110" height="45" viewBox="0 0 110 45">
    <path d="M22,0 L110,0 L110,45 L2,45 Q14,38 12,22 Q10,6 22,0 Z" fill="var(--gold)"/>
  </svg>
  <span class="page-number">01</span>
</div>
</body>
</html>
```